Construction business card

I need a new business card, they can connect with my logo, brand.
What we do is residential house , design and build
I like: Navy blue / black
I attached our logo, brand,
and, some idea for business card.

```html
<!DOCTYPE html>
<html lang="en">
<head>
<meta charset="utf-8">
<title>Harwell Building Co – Business Card</title>
<link rel="stylesheet" href="https://fonts.googleapis.com/css2?family=Lato:wght@400;700&display=swap">
<style>
  :root {
    --bg: #2b2b2b;
    --card: #0a0a0a;
    --blue: #3d86f2;
    --white: #ffffff;
    --text: #e9e9e9;
  }
  * { margin: 0; padding: 0; box-sizing: border-box; }
  html, body {
    width: 1200px; height: 1200px; overflow: hidden;
    background: var(--bg);
    font-family: "Lato", Arial, sans-serif;
  }
  .card {
    position: absolute;
    left: 272px;
    width: 688px; height: 394px;
    background: var(--card);
    border-radius: 28px;
  }
  .card--front { top: 194px; }
  .card--back { top: 618px; }

  .brand {
    position: absolute;
    display: flex; align-items: center; gap: 12px;
    color: var(--white);
    font-weight: 700;
  }
  .brand__dot { background: var(--blue); flex: none; }
  .brand__name { text-transform: uppercase; letter-spacing: 0.04em; line-height: 1.15; }

  .card--front .brand { left: 70px; top: 198px; transform: translateY(-50%); width: 240px; }
  .card--front .brand__dot { width: 20px; height: 20px; }
  .card--front .brand__name { font-size: 28px; }

  .card--back .brand { left: 50%; top: 50%; transform: translate(-50%, -50%); gap: 18px; white-space: nowrap; }
  .card--back .brand__dot { width: 30px; height: 30px; }
  .card--back .brand__name { font-size: 42px; }

  .divider {
    position: absolute; left: 342px; top: 74px;
    width: 2px; height: 244px;
    background: linear-gradient(var(--card), #2f5fae 20%, #2f5fae 80%, var(--card));
  }
  .contact { position: absolute; left: 376px; top: 70px; color: var(--text); }
  .contact__name {
    color: var(--blue); font-size: 28px; font-weight: 700;
    letter-spacing: 0.01em; line-height: 1;
  }
  .contact__role { font-size: 18px; margin-top: 6px; }
  .contact__list { list-style: none; margin-top: 22px; }
  .contact__item {
    display: flex; align-items: center; gap: 14px;
    font-size: 18px; height: 31px;
  }
  .contact__icon { width: 20px; height: 20px; flex: none; fill: var(--blue); }
  .contact__address { font-size: 18px; line-height: 26px; margin-top: 18px; }
</style>
</head>
<body>
  <section class="card card--front">
    <div class="brand">
      <span class="brand__dot"></span>
      <span class="brand__name">Harwell<br>Building Co</span>
    </div>
    <div class="divider"></div>
    <div class="contact">
      <h1 class="contact__name">DANIEL MORROW</h1>
      <p class="contact__role">Owner</p>
      <ul class="contact__list">
        <li class="contact__item">
          <svg class="contact__icon" viewBox="0 0 24 24"><path d="M6.6 10.8a15.1 15.1 0 0 0 6.6 6.6l2.2-2.2a1 1 0 0 1 1-.25 11.4 11.4 0 0 0 3.6.57 1 1 0 0 1 1 1V20a1 1 0 0 1-1 1A17 17 0 0 1 3 4a1 1 0 0 1 1-1h3.5a1 1 0 0 1 1 1c0 1.25.2 2.45.57 3.6a1 1 0 0 1-.25 1z"/></svg>
          <span>0400 555 018</span>
        </li>
        <li class="contact__item">
          <svg class="contact__icon" viewBox="0 0 24 24"><path d="M2 5h20v2l-10 6L2 7z"/><path d="M2 9l10 6 10-6v10H2z"/></svg>
          <span>hello@harwellbuild.com</span>
        </li>
        <li class="contact__item">
          <svg class="contact__icon" viewBox="0 0 24 24"><circle cx="12" cy="12" r="10"/><path d="M8 5c2 1 1 3 3 3s1 3-1 3-3 1-2 3 3 1 3 4M16 7c-1 2 1 3 2 2M15 14c1 1 2 3 1 5" stroke="#0a0a0a" stroke-width="1.6" fill="none"/></svg>
          <span>www.harwellbuild.com</span>
        </li>
      </ul>
      <p class="contact__address">27 Carrow Street,<br>Elmwood, Vic 3180</p>
    </div>
  </section>

  <section class="card card--back">
    <div class="brand">
      <span class="brand__dot"></span>
      <span class="brand__name">Harwell Building Co</span>
    </div>
  </section>
</body>
</html>
```